New Fitness Company looking for creative website design

I am building a new fitness matching service. To match customers looking for fitness services to professionals that meet their requirements

My business will have 5 different divisions and I would like to have tabs for each division

1. Matching client to trainer - I need to have video upload capability on the site
2. Corporate personal training services

-The site needs a shopping cart as well as payment capability.
- I am looking for the site to be bright and inviting as well as have clients and trainers going through some type of workout on the main page.
- I also need the capability to capture email addresses
- We are going to have a section that ask the customer questions to match up the trainer so that needs to be a part of the site
-Ability to have trainers rated in a 1 star to 5 stars as well as reviews
- Site should be inviting, bright and vibrant colors that catch the eye and is easy to use
- Similar sites for inspiration are www.zavrello.com where you give a description of how the service works, short video and various services.

Target Market(s)

mid income to high income, mix of female and male customers

Industry/Entity Type

Fitness

Coding

Coded - Design and coding required

Number of Pages Required

5+ page

Font styles to use
Serif
Sans Serif

Requirements
Must have
• Must have the logos that I provided in the website
Should not have
• Not looking for bodybuilders on website. This is for everyday people that are interested in staying in shape and working out. So active fit people will resonate with my prospects

```html
<!DOCTYPE html>
<html lang="en">
<head>
<meta charset="utf-8">
<title>Vantoro Fitness</title>
<link rel="stylesheet" href="https://fonts.googleapis.com/css2?family=Open+Sans:wght@400;600;700;800&family=Raleway:wght@600;700;800&display=swap">
<style>
:root{
  --green:#3aa935;
  --green-dark:#2e8f2a;
  --orange:#efa02c;
  --orange-deep:#e8921c;
  --ink:#333333;
  --muted:#777777;
  --light:#f4f4f4;
  --line:#dddddd;
  --price:#e04a3a;
  --footer:#464646;
  --footer-text:#d0d0d0;
  --star:#f0a030;
}
*{box-sizing:border-box;margin:0;padding:0}
html,body{width:1200px;height:3309px;overflow:hidden}
body{position:relative;font-family:"Open Sans",Arial,sans-serif;color:var(--ink);background:#fff}
.abs{position:absolute}
a{color:inherit;text-decoration:none}

/* header */
.site-header{position:absolute;left:0;top:0;width:1200px;height:101px;background:#fff;border-top:4px solid var(--green)}
.brand{position:absolute;left:99px;top:26px;display:flex;align-items:center;gap:10px;font-weight:800;font-size:26px;color:var(--green);letter-spacing:1px}
.brand-dot{width:26px;height:26px;border-radius:50%;background:var(--orange)}
.main-nav{position:absolute;left:287px;top:40px;display:flex;gap:26px;font-family:"Raleway",sans-serif;font-weight:700;font-size:13px;color:#333}
.main-nav .active{color:var(--green)}
.search{position:absolute;left:635px;top:31px;width:225px;height:36px;border:1px solid #ccc;border-radius:3px;font-size:11px;color:#999;padding:10px 12px}
.search svg{position:absolute;right:10px;top:10px}
.account{position:absolute;left:887px;top:42px;font-size:11px;color:#666;font-weight:600;letter-spacing:.3px}

/* hero */
.hero{position:absolute;left:0;top:101px;width:1200px;height:424px;background:linear-gradient(100deg,#e9c4b8 0%,#c9a08a 30%,#8a7a72 55%,#d26a6a 75%,#c8b6a8 100%)}
.hero-title{position:absolute;left:0;width:1200px;top:168px;text-align:center;color:#fff;font-family:"Raleway",sans-serif;font-weight:800;font-size:50px;letter-spacing:1px}
.btn{display:inline-block;background:var(--green);color:#fff;font-weight:700;text-align:center;border-radius:3px}
.hero .btn{position:absolute;left:512px;top:254px;width:176px;height:49px;line-height:49px;font-size:15px}
.hero-arrow{position:absolute;top:190px}
.hero-dots{position:absolute;left:572px;top:376px;display:flex;gap:5px}
.hero-dots span{width:12px;height:12px;border-radius:50%;background:#e0a040;border:2px solid #fff}

/* section heads */
.sec-title{position:absolute;left:0;width:1200px;text-align:center;font-family:"Raleway",sans-serif;font-weight:700;font-size:23px;color:#333;letter-spacing:.5px}
.sec-mark{position:absolute;left:520px;width:160px;height:20px}
.sec-mark::before,.sec-mark::after{content:"";position:absolute;top:9px;width:58px;height:2px;background:var(--line)}
.sec-mark::before{left:0}.sec-mark::after{right:0}
.sec-mark i{position:absolute;left:70px;top:0;width:20px;height:20px;border-radius:50%;border:3px solid var(--green)}
.on-orange .sec-mark::before,.on-orange .sec-mark::after{background:rgba(255,255,255,.6)}
.on-orange .sec-mark i{border-color:#fff}

/* corporate */
.corporate{position:absolute;left:0;top:525px;width:1200px;height:428px;background:#fff}
.corporate .photo{position:absolute;left:618px;top:0;width:582px;height:428px;background:linear-gradient(90deg,#ffffff 0%,#eee6ea 35%,#e3c7d6 60%,#c8c8c8 100%)}
.corporate .copy{position:absolute;left:99px;top:152px;width:540px;font-size:12.5px;line-height:21px;color:#666}
.corporate .copy p+p{margin-top:22px}
.learn{font-weight:700;font-size:12px;color:var(--green)}
.corporate .learn{position:absolute;left:99px;top:312px}

/* matching */
.matching{position:absolute;left:0;top:953px;width:1200px;height:600px;background:var(--light)}
.deco{position:absolute}
.video{position:absolute;left:276px;top:128px;width:648px;height:430px;background:#111}
.video-top{height:22px;background:#111;color:#fff;font-size:10px;font-weight:700;padding:5px 10px;display:flex;justify-content:space-between}
.video-frame{position:absolute;left:0;top:22px;width:648px;height:380px;background:linear-gradient(110deg,#4a5a6a 0%,#8a9aa8 35%,#e8c8b0 55%,#c9b060 80%,#3a4050 100%)}
.video-play{position:absolute;left:294px;top:165px;width:60px;height:50px}
.video-bar{position:absolute;left:0;bottom:0;width:648px;height:28px;background:#0c0c0c;display:flex;align-items:center;gap:12px;padding:0 10px;color:#fff;font-size:11px}
.video-progress{position:absolute;left:0;bottom:28px;width:648px;height:3px;background:#555}
.video-progress span{display:block;width:40px;height:3px;background:#c22}

/* faq */
.faq{position:absolute;left:0;top:1553px;width:1200px;height:404px;background:linear-gradient(180deg,var(--orange) 0%,var(--orange-deep) 100%)}
.faq .sec-title{color:#fff}
.faq-col{position:absolute;top:157px;width:310px;color:#fff}
.faq-col h3{font-size:12.5px;font-weight:700;margin-bottom:12px}
.faq-col p{font-size:11.5px;line-height:18px;margin-bottom:10px}
.faq-col .learn{color:#fff}
.faq .btn{position:absolute;left:465px;top:313px;width:272px;height:49px;line-height:49px;font-size:13px}

/* trainers */
.trainers{position:absolute;left:0;top:1957px;width:1200px;height:576px;background:#f7f7f7}
.trainer{position:absolute;top:141px;width:210px;text-align:center}
.trainer-photo{width:210px;height:298px;background:#fff;border:1px solid #e4e4e4;padding:10px}
.trainer-photo div{width:100%;height:100%}
.trainer h4{margin-top:22px;font-size:14px;font-weight:700;color:#333}
.trainer p{margin-top:8px;font-size:11.5px;line-height:17px;color:#777}
.stars{margin-top:6px;color:var(--star);font-size:12px;letter-spacing:1px}

/* products */
.products{position:absolute;left:0;top:2533px;width:1200px;height:533px;background:#fff}
.product{position:absolute;top:112px;width:316px}
.product-photo{position:relative;width:316px;height:234px;background:#f0f0f0;border:1px solid #e6e6e6}
.product-photo .item{position:absolute;left:108px;top:16px;width:100px;height:190px;border-radius:8px}
.ribbon{position:absolute;left:0;top:190px;width:100%;height:33px;background:linear-gradient(90deg,var(--green) 0%,rgba(58,169,53,.75) 70%,rgba(58,169,53,.15) 100%);color:#fff;font-weight:700;font-size:14px;padding:7px 14px}
.product h4{margin-top:50px;font-size:13px;font-weight:700}
.product p{margin-top:8px;font-size:11.5px;line-height:17px;color:#777}
.price{margin-top:12px;color:var(--price);font-weight:700;font-size:16px}

/* footer */
.site-footer{position:absolute;left:0;top:3066px;width:1200px;height:243px;background:var(--footer);color:var(--footer-text)}
.f-col{position:absolute;top:34px;font-size:11.5px;line-height:21px}
.f-col h5{color:#fff;font-size:13px;font-weight:700;margin-bottom:6px}
.newsletter p{width:220px;line-height:17px}
.subscribe{position:absolute;left:518px;top:119px;display:flex}
.subscribe .field{width:239px;height:34px;background:#555;border:1px solid #666;color:#aaa;font-size:11px;padding:9px 12px}
.subscribe .go{width:95px;height:34px;line-height:34px;background:var(--green);color:#fff;font-weight:700;font-size:11px;text-align:center}
.footer-name{position:absolute;left:915px;top:60px;width:188px;text-align:center;font-weight:800;font-size:30px;color:#5c5c5c}
.copyright{position:absolute;left:99px;top:207px;font-size:11px}
.socials{position:absolute;left:992px;top:204px;display:flex;gap:8px}
.socials span{width:18px;height:18px;background:#d8d8d8;border-radius:2px}
</style>
</head>
<body>

<header class="site-header">
  <div class="brand"><span class="brand-dot"></span>VANTORO</div>
  <nav class="main-nav">
    <a class="active">HOME</a><a>TRAINING</a><a>TRAINER</a><a>FAQ</a><a>STORE</a>
  </nav>
  <div class="search">SEARCH
    <svg width="13" height="13" viewBox="0 0 13 13"><circle cx="5.5" cy="5.5" r="4" fill="none" stroke="#777" stroke-width="1.6"/><line x1="8.5" y1="8.5" x2="12" y2="12" stroke="#777" stroke-width="1.8"/></svg>
  </div>
  <div class="account">LOG IN &nbsp;/&nbsp; REGISTER &nbsp;/&nbsp; CART(0)</div>
</header>

<section class="hero">
  <div class="abs" style="left:0;top:0;width:1200px;height:424px" role="img" aria-label="Group of people exercising with red dumbbells in a bright studio"></div>
  <h1 class="hero-title">VANTORO FITNESS</h1>
  <a class="btn">GET STARTED</a>
  <svg class="hero-arrow" style="left:34px" width="14" height="24" viewBox="0 0 14 24"><polyline points="12,2 2,12 12,22" fill="none" stroke="#fff" stroke-width="2.5"/></svg>
  <svg class="hero-arrow" style="left:1152px" width="14" height="24" viewBox="0 0 14 24"><polyline points="2,2 12,12 2,22" fill="none" stroke="#fff" stroke-width="2.5"/></svg>
  <div class="hero-dots"><span></span><span></span><span></span></div>
</section>

<section class="corporate">
  <div class="photo" role="img" aria-label="Woman in pink top resting on a grey exercise ball with a towel"></div>
  <h2 class="sec-title" style="top:42px;width:740px">CORPORATE PERSONAL TRAINING</h2>
  <div class="sec-mark" style="left:290px;top:88px"><i></i></div>
  <div class="copy">
    <p>Sed ut perspiciatis unde omnis iste natus error sit voluptatem accusantium doloremque laud antium, totam rem aperiam.</p>
    <p>Nemo enim ipsam voluptatem quia voluptas sit aspernatur au dit aut fugit, sed quia consequ-untur magni dolores eos qui ratione voluptatem sequi nesciun<br>Neque porro quisquam est, qui dolorem ipsum qui..</p>
  </div>
  <a class="learn">Learn More »</a>
</section>

<section class="matching">
  <div class="deco" style="left:0;top:0;width:276px;height:280px;background:linear-gradient(135deg,#f4f4f4 0%,#b8bcc0 40%,#3a7ed8 75%,#f4f4f4 100%)" role="img" aria-label="Blue skipping rope"></div>
  <div class="deco" style="left:938px;top:0;width:262px;height:280px;background:linear-gradient(200deg,#c8d860 0%,#e8a040 40%,#f4f4f4 90%)" role="img" aria-label="Green sneakers"></div>
  <div class="deco" style="left:926px;top:366px;width:274px;height:234px;background:radial-gradient(circle at 60% 50%,#a8a8a8 0%,#c8c8c8 45%,#f4f4f4 75%)" role="img" aria-label="Steel dumbbells"></div>
  <h2 class="sec-title" style="top:46px">MATCHING CLIENT TO TRAINER</h2>
  <div class="sec-mark" style="top:85px"><i></i></div>
  <div class="video">
    <div class="video-top"><span>MATCHING CLIENT TO TRAINER</span><span>◷ &nbsp;⋯</span></div>
    <div class="video-frame" role="img" aria-label="Video still of a woman training on an exercise bike in a gym"></div>
    <svg class="video-play" viewBox="0 0 60 50"><rect width="60" height="50" rx="8" fill="#222" opacity=".7"/><polygon points="24,15 40,25 24,35" fill="#fff"/></svg>
    <div class="video-progress"><span></span></div>
    <div class="video-bar">
      <svg width="10" height="12" viewBox="0 0 10 12"><polygon points="0,0 10,6 0,12" fill="#fff"/></svg>
      <svg width="10" height="12" viewBox="0 0 10 12"><rect x="0" y="0" width="3" height="12" fill="#fff"/><rect x="7" y="0" width="3" height="12" fill="#fff"/></svg>
      <svg width="11" height="11" viewBox="0 0 11 11"><rect width="11" height="11" fill="#fff"/></svg>
      <svg width="14" height="12" viewBox="0 0 14 12"><polygon points="0,4 4,4 8,0 8,12 4,8 0,8" fill="#fff"/><path d="M10 3 Q13 6 10 9" stroke="#fff" fill="none"/></svg>
      <span>1.08/12.06</span>
      <span style="flex:1"></span>
      <span>⚙</span><span>▮▮</span>
      <svg width="14" height="14" viewBox="0 0 14 14"><path d="M1 5V1h4M9 1h4v4M13 9v4H9M5 13H1V9" stroke="#fff" stroke-width="2" fill="none"/></svg>
    </div>
  </div>
</section>

<section class="faq on-orange">
  <div class="abs" style="left:0;top:0;width:1200px;height:404px;opacity:.12;background:linear-gradient(90deg,#fff,#8a4a00,#fff)" role="img" aria-label="Faint photo of a group workout class"></div>
  <h2 class="sec-title" style="top:40px">FREQUENTLY ASKED QUESTIONS</h2>
  <div class="sec-mark" style="top:80px"><i></i></div>
  <div class="faq-col" style="left:99px"><h3>WHAT IF I CAN'T MAKE IT TO A CLASS?</h3><p>At vero eos et accusamus et iusto odio dignissimos duc imus qui blanditiis praesentium voluptatum deleniti at que corrupti quos dolores et quas mo..</p><a class="learn">Learn More »</a></div>
  <div class="faq-col" style="left:446px"><h3>WHAT IF I CAN'T MAKE IT TO A CLASS?</h3><p>At vero eos et accusamus et iusto odio dignissimos duc imus qui blanditiis praesentium voluptatum deleniti at que corrupti quos dolores et quas mo..</p><a class="learn">Learn More »</a></div>
  <div class="faq-col" style="left:792px"><h3>WHAT IF I CAN'T MAKE IT TO A CLASS?</h3><p>At vero eos et accusamus et iusto odio dignissimos duc imus qui blanditiis praesentium voluptatum deleniti at que corrupti quos dolores et quas mo..</p><a class="learn">Learn More »</a></div>
  <a class="btn">GET MORE DETAIL IN OUR FAQ</a>
</section>

<section class="trainers">
  <h2 class="sec-title" style="top:46px">OUR TRAINER</h2>
  <div class="sec-mark" style="top:86px"><i></i></div>
  <div class="trainer" style="left:99px"><div class="trainer-photo"><div role="img" aria-label="Female trainer in pink tank top and grey leggings" style="background:linear-gradient(180deg,#fff 5%,#e8a8c0 35%,#6a6a70 70%,#fff 98%)"></div></div><h4>MARGO</h4><p>Nemo enim ipsam voluptatem quia voluptas sit aspernatur dolo..</p><div class="stars">★★★★★</div></div>
  <div class="trainer" style="left:364px"><div class="trainer-photo"><div role="img" aria-label="Male trainer in black t-shirt and shorts holding a clipboard" style="background:linear-gradient(180deg,#fff 5%,#2a2a2a 35%,#3a3a3a 65%,#d8b090 85%,#fff 98%)"></div></div><h4>JOHN MARTIN</h4><p>Nemo enim ipsam voluptatem quia voluptas sit aspernatur dolo..</p><div class="stars">★★★★★</div></div>
  <div class="trainer" style="left:627px"><div class="trainer-photo"><div role="img" aria-label="Female trainer in yellow top and black shorts" style="background:linear-gradient(180deg,#fff 5%,#f0e070 35%,#2a2a2a 60%,#d8b090 80%,#fff 98%)"></div></div><h4>AGNES</h4><p>Nemo enim ipsam voluptatem quia voluptas sit aspernatur dolo..</p><div class="stars">★★★★★</div></div>
  <div class="trainer" style="left:889px"><div class="trainer-photo"><div role="img" aria-label="Male trainer in grey t-shirt and black shorts" style="background:linear-gradient(180deg,#fff 5%,#707a88 35%,#2a2a2a 60%,#d8b090 80%,#fff 98%)"></div></div><h4>GRU</h4><p>Nemo enim ipsam voluptatem quia voluptas sit aspernatur dolo..</p><div class="stars">★★★★★</div></div>
</section>

<section class="products">
  <h2 class="sec-title" style="top:34px">FITNESS PRODUCTS</h2>
  <div class="sec-mark" style="top:78px"><i></i></div>
  <div class="product" style="left:99px"><div class="product-photo"><div class="item" role="img" aria-label="Black energy drink can" style="background:linear-gradient(90deg,#111,#444,#111)"></div><div class="ribbon">ORDER AND SAVE 20%</div></div><h4>FINIBUS BONORUM ET</h4><p>Nam libero tempore, cum soluta nobis est eligendi optio cumque nihil impedit quo minus..</p><div class="price">$ 25:00</div></div>
  <div class="product" style="left:443px"><div class="product-photo"><div class="item" role="img" aria-label="Blue and silver energy drink can" style="background:linear-gradient(90deg,#1a3aa8,#c8ccd8,#1a3aa8)"></div><div class="ribbon">ORDER AND SAVE 20%</div></div><h4>FINIBUS BONORUM ET</h4><p>Nam libero tempore, cum soluta nobis est eligendi optio cumque nihil impedit quo minus..</p><div class="price">$ 25:00</div></div>
  <div class="product" style="left:785px"><div class="product-photo"><div class="item" role="img" aria-label="Black supplement tub with green label" style="left:93px;width:130px;border-radius:14px;background:linear-gradient(180deg,#1c1c1c 0%,#2a2a2a 40%,#3aa935 55%,#1c1c1c 70%)"></div><div class="ribbon">ORDER AND SAVE 20%</div></div><h4>FINIBUS BONORUM ET</h4><p>Nam libero tempore, cum soluta nobis est eligendi optio cumque nihil impedit quo minus..</p><div class="price">$ 25:00</div></div>
</section>

<footer class="site-footer">
  <div class="f-col" style="left:99px"><h5>INFORMATION</h5>Home<br>Training<br>Trainer<br>FAQ<br>Store</div>
  <div class="f-col" style="left:287px"><h5>QUICK LINKS</h5>FAQ<br>Blog<br>Help Center<br>Jobs<br>Partners</div>
  <div class="f-col" style="left:390px;top:61px">Press<br>About<br>Privacy<br>Terms</div>
  <div class="f-col newsletter" style="left:518px"><h5>NEWSLETTER SUBSCRIPTION</h5><p>Register Yourm email address to get information about us</p></div>
  <div class="subscribe"><div class="field">Email Address</div><div class="go">SUBSCRIBE</div></div>
  <div class="footer-name">VANTORO</div>
  <div class="copyright">© 2015 Vantoro.All rights reserved.</div>
  <div class="socials"><span></span><span></span><span></span><span></span><span></span></div>
</footer>

</body>
</html>
```